Quorbelt

I have attached a doc file with the information for the brochure as well as a video, logos also.

Requirements
Must have
• It is a 8.5 x 11 foldable brochure.

```html
<!DOCTYPE html>
<html lang="en">
<head>
<meta charset="utf-8">
<title>Quorbelt Brochure</title>
<link href="https://fonts.googleapis.com/css2?family=Montserrat:wght@600;700;800&display=swap" rel="stylesheet">
<style>
  :root {
    --backdrop: #bdbdbf;
    --black: #000000;
    --white: #ffffff;
    --brand-red: #ad252c;
    --blue: #1476bd;
    --green: #05693a;
    --purple: #9c1f63;
    --ink: #111111;
    --device-dark: #2a2a2a;
    --device-mid: #6b6b6b;
  }
  html, body {
    margin: 0;
    padding: 0;
    width: 1200px;
    height: 1000px;
    overflow: hidden;
    background: var(--backdrop);
  }
  .canvas {
    position: relative;
    width: 1200px;
    height: 1000px;
    font-family: "Montserrat", Arial, sans-serif;
  }
  .artwork {
    position: absolute;
    left: 0;
    top: 0;
  }
  .label {
    position: absolute;
    color: var(--white);
    font-weight: 700;
    text-align: center;
    transform: translateX(-50%);
    line-height: 1.3;
  }
  .claim-title {
    left: 232px;
    top: 162px;
    font-size: 26px;
    line-height: 1.36;
    width: 260px;
  }
  .claim-mail { left: 478px; top: 200px; font-size: 16px; width: 170px; }
  .claim-demand { left: 382px; top: 343px; font-size: 16px; width: 160px; }
  .claim-store { left: 232px; top: 389px; font-size: 16px; width: 180px; line-height: 1.38; }

  .brand {
    position: absolute;
    left: 660px;
    top: 160px;
    display: flex;
    align-items: center;
    gap: 18px;
  }
  .brand-dot {
    width: 84px;
    height: 84px;
    border-radius: 50%;
    background: var(--brand-red);
  }
  .brand-name {
    color: var(--white);
    font-size: 50px;
    font-weight: 700;
    letter-spacing: 1px;
  }

  .coverage {
    position: absolute;
    left: 858px;
    top: 378px;
    transform: translateX(-50%);
    text-align: center;
    width: 480px;
    white-space: nowrap;
  }
  .coverage-head {
    color: var(--brand-red);
    font-size: 26px;
    font-weight: 800;
    margin: 0 0 2px;
  }
  .coverage-list {
    color: var(--ink);
    font-size: 21px;
    font-weight: 700;
    line-height: 1.33;
    margin: 0;
  }

  .devices {
    position: absolute;
    left: 685px;
    top: 500px;
    width: 350px;
    height: 330px;
    border-radius: 10px;
    background: linear-gradient(160deg, var(--device-mid), var(--device-dark));
  }
  .site-footer {
    position: absolute;
    left: 858px;
    top: 846px;
    transform: translateX(-50%);
    color: var(--white);
    font-size: 12px;
    font-weight: 600;
  }

  .contact {
    position: absolute;
    left: 340px;
    top: 700px;
    transform: translateX(-50%);
    text-align: center;
    width: 260px;
  }
  .contact-brand {
    color: var(--brand-red);
    font-size: 26px;
    font-weight: 700;
    margin: 0 0 50px;
  }
  .contact-head {
    color: var(--brand-red);
    font-size: 22px;
    font-weight: 700;
    margin: 0 0 14px;
  }
  .contact-lines {
    color: var(--ink);
    font-size: 11px;
    font-weight: 600;
    line-height: 1.3;
    margin: 0;
  }
</style>
</head>
<body>
<div class="canvas">
  <svg class="artwork" width="1200" height="1000" viewBox="0 0 1200 1000" aria-hidden="true">
    <defs>
      <clipPath id="panel-clip">
        <rect x="82" y="100" width="1036" height="800"/>
      </clipPath>
      <linearGradient id="red-sweep" x1="0" y1="0" x2="1" y2="1">
        <stop offset="0" stop-color="#a8202a"/>
        <stop offset="1" stop-color="#d15858"/>
      </linearGradient>
    </defs>
    <g clip-path="url(#panel-clip)">
      <rect class="panel-black" x="82" y="100" width="1036" height="800" fill="var(--black)"/>
      <path class="band-red" d="M1118 322 C 800 330, 400 355, 230 478 C 140 545, 95 640, 82 700 L82 900 L125 900 C 140 700, 200 545, 330 470 C 500 382, 800 338, 1118 330 Z" fill="var(--brand-red)"/>
      <path class="body-white" d="M1118 330 C 800 338, 500 382, 330 470 C 200 545, 140 700, 125 900 L1118 900 Z" fill="var(--white)"/>
      <path class="sweep-red" d="M475 900 C 560 700, 800 540, 1118 485 L1118 900 Z" fill="url(#red-sweep)"/>
      <circle cx="480" cy="225" r="99" fill="var(--blue)" stroke="var(--white)" stroke-width="2"/>
      <circle cx="382" cy="364" r="101" fill="var(--green)" stroke="var(--white)" stroke-width="2"/>
      <circle cx="232" cy="445" r="102" fill="var(--purple)" stroke="var(--white)" stroke-width="2"/>
      <circle cx="232" cy="205" r="160" fill="var(--brand-red)" stroke="var(--white)" stroke-width="2.5"/>
    </g>
  </svg>

  <div class="label claim-title">3 Different ways to file a claim</div>
  <div class="label claim-mail">Mail-in service<br>(free shipping)</div>
  <div class="label claim-demand">Quorbelt<br>On-Demand</div>
  <div class="label claim-store">Reimbursement<br>at your<br>local store<br>or Tech Desk<br>(your choice)</div>

  <div class="brand">
    <div class="brand-dot"></div>
    <div class="brand-name">QUORBELT</div>
  </div>

  <div class="coverage">
    <p class="coverage-head">WE COVER ALL</p>
    <p class="coverage-list">smartphones • e-pads • x-phones<br>smart watches • tablets</p>
  </div>

  <div class="devices" role="img" aria-label="Desktop monitor, tablet and smartphone showing the Quorbelt name"></div>
  <div class="site-footer">www.quorbelt.com</div>

  <div class="contact">
    <p class="contact-brand">QUORBELT</p>
    <p class="contact-head">CONTACT US</p>
    <p class="contact-lines">phone: 001-9876-543<br>email: info@quorbelt.com<br>web: www.quorbelt.com</p>
  </div>
</div>
</body>
</html>
```